GJ & DW Fencing Pty Ltd

We already have an existing logo created by Pixel Harbour however we have restructured to a company. We would like someone to add Pty Ltd to our business name please.

Colors

Designer to choose only greyscale colors for use in the design.

```html
<!DOCTYPE html>
<html lang="en">
<head>
<meta charset="utf-8">
<title>GJ &amp; DW Fencing Pty Ltd – Business Card</title>
<link href="https://fonts.googleapis.com/css2?family=Lato:wght@400&family=Merriweather:wght@700&display=swap" rel="stylesheet">
<style>
  :root {
    --backdrop: #2a2a2a;
    --card-white: #ffffff;
    --card-black: #000000;
    --ink: #111111;
    --rule: #9a9a9a;
    --art-light: #e6e6e6;
    --art-dark: #0a0a0a;
  }
  * { margin: 0; padding: 0; box-sizing: border-box; }
  html, body { width: 1200px; height: 1200px; overflow: hidden; }
  body { background: var(--backdrop); position: relative; font-family: "Lato", Arial, sans-serif; }

  .card {
    position: absolute;
    top: 310px;
    height: 594px;
    box-shadow: 0 4px 10px rgba(0,0,0,0.45);
  }
  .card-front { left: 234px; width: 364px; background: var(--card-white); color: var(--ink); }
  .card-back { left: 627px; width: 369px; background: var(--card-black); }

  .brand-name {
    position: absolute;
    left: 0; right: 0;
    top: 118px;
    text-align: center;
    font-family: "Merriweather", Georgia, serif;
    font-weight: 700;
    color: var(--ink);
    line-height: 1.05;
  }
  .brand-name .brand-initials { display: block; font-size: 46px; letter-spacing: 1px; }
  .brand-name .brand-trade { display: block; font-size: 24px; letter-spacing: 1px; margin-top: 4px; }
  .brand-name .brand-entity { display: block; font-size: 11px; letter-spacing: 2px; margin-top: 6px; }

  .holder-name {
    position: absolute;
    left: 0; right: 0;
    top: 346px;
    text-align: center;
    font-family: "Merriweather", Georgia, serif;
    font-weight: 700;
    font-size: 18px;
    letter-spacing: 0.5px;
  }

  .contact-list { position: absolute; left: 0; right: 0; top: 385px; list-style: none; }
  .contact-item { position: relative; text-align: center; height: 56px; }
  .contact-item:nth-child(2) { height: 56px; }
  .contact-icon-row {
    position: relative;
    height: 28px;
    display: flex;
    justify-content: center;
    align-items: center;
  }
  .contact-icon-row::before,
  .contact-icon-row::after {
    content: "";
    width: 44px;
    height: 1px;
    background: var(--rule);
    margin: 0 6px;
  }
  .contact-icon { width: 28px; height: 28px; }
  .contact-text { display: block; font-size: 17px; line-height: 26px; margin-top: 1px; }

  .back-art {
    position: absolute;
    left: 20px; top: 150px;
    width: 330px; height: 430px;
    background: radial-gradient(ellipse at 50% 45%, var(--art-light) 0%, #bdbdbd 45%, var(--art-dark) 75%);
  }
</style>
</head>
<body>
  <section class="card card-front">
    <h1 class="brand-name">
      <span class="brand-initials">GJ &amp; DW</span>
      <span class="brand-trade">FENCING</span>
      <span class="brand-entity">PTY LTD</span>
    </h1>

    <h2 class="holder-name">TOM CALDER</h2>

    <ul class="contact-list">
      <li class="contact-item">
        <div class="contact-icon-row">
          <svg class="contact-icon" viewBox="0 0 28 28" aria-hidden="true">
            <circle cx="14" cy="14" r="14" fill="#111"/>
            <path d="M8 11c0-2 2-3 6-3s6 1 6 3v1h-3v-1.5h-6V12H8z M9 19l2-5h6l2 5z" fill="#fff"/>
          </svg>
        </div>
        <span class="contact-text">044 5120947</span>
      </li>
      <li class="contact-item">
        <div class="contact-icon-row">
          <svg class="contact-icon" viewBox="0 0 28 28" aria-hidden="true">
            <circle cx="14" cy="14" r="14" fill="#111"/>
            <rect x="8" y="9.5" width="12" height="9" fill="#fff"/>
            <path d="M8 9.5l6 5 6-5" fill="none" stroke="#111" stroke-width="1.2"/>
          </svg>
        </div>
        <span class="contact-text">gjdwfencing@mailbox.net</span>
      </li>
      <li class="contact-item">
        <div class="contact-icon-row">
          <svg class="contact-icon" viewBox="0 0 28 28" aria-hidden="true">
            <circle cx="14" cy="14" r="14" fill="#111"/>
            <path d="M14 6a5 5 0 0 0-5 5c0 4 5 10 5 10s5-6 5-10a5 5 0 0 0-5-5z" fill="#fff"/>
            <circle cx="14" cy="11" r="2" fill="#111"/>
          </svg>
        </div>
        <span class="contact-text">PO Box 418 Dunmore WA 6512</span>
      </li>
    </ul>
  </section>

  <section class="card card-back">
    <div class="back-art" role="img" aria-label="Illustration of a white sheep standing on a black background"></div>
  </section>
</body>
</html>
```